KBT Business Cards

We require business cards for our business. We would like a matte black back to the card, with our logo centred in the middle. The front side of the card is open to design.

Target Market(s)

Clients looking for legal services (professional)

Industry/Entity Type

Legal

Contact Information for Business Card

Doran Kelbrath
Partner
Mobile: 0461 738 524
Email: doran@kbtlaw.co
Website: www.kbtlaw.co
Level 3, 118 Wendmore Street
Sydney NSW 2000

Font styles to use
Other font styles liked:
• Avenir

Colors
f04a50
ffffff
1b1b1b

Requirements
Must have
• Black back with logo included in the centre of the card.
• Our font is Avenir.

```html
<!DOCTYPE html>
<html lang="en">
<head>
<meta charset="utf-8">
<title>KBT Business Cards</title>
<link rel="stylesheet" href="https://fonts.googleapis.com/css2?family=Roboto:wght@400;500&display=swap">
<style>
  :root {
    --backdrop: #5e5e5e;
    --card-white: #ffffff;
    --card-black: #231f20;
    --ink: #1b1b1b;
    --accent: #c41e4a;
    --light-text: #e6e6e6;
  }
  * { margin: 0; padding: 0; box-sizing: border-box; }
  html, body { width: 1200px; height: 802px; overflow: hidden; }
  body {
    background: var(--backdrop);
    font-family: "Roboto", sans-serif;
    position: relative;
  }
  .card {
    position: absolute;
    top: 274px;
    width: 443px;
    height: 264px;
    background: var(--card-white);
    overflow: hidden;
    box-shadow: 0 4px 10px rgba(0,0,0,0.35);
  }
  .card--contact { left: 136px; }
  .card--brand { left: 624px; }

  .contact-panel {
    position: absolute;
    inset: 0;
    width: 100%;
    height: 100%;
  }
  .contact-details {
    position: absolute;
    right: 36px;
    top: 82px;
    text-align: right;
    color: var(--light-text);
  }
  .contact-name {
    color: var(--accent);
    font-weight: 500;
    font-size: 16px;
    letter-spacing: 0.2px;
    line-height: 1.1;
  }
  .contact-role {
    font-size: 13px;
    line-height: 1.2;
    margin-bottom: 10px;
  }
  .contact-line {
    font-size: 12.5px;
    line-height: 16px;
    display: flex;
    justify-content: flex-end;
    align-items: center;
    gap: 3px;
  }
  .contact-line svg { width: 9px; height: 9px; fill: var(--accent); }
  .contact-address {
    font-size: 12.5px;
    line-height: 16px;
    margin-top: 6px;
    color: #cfcfcf;
  }

  .brand-lockup {
    position: absolute;
    left: 50%;
    top: 50%;
    transform: translate(-50%, -50%);
    display: flex;
    align-items: center;
    gap: 12px;
  }
  .brand-square {
    width: 14px;
    height: 14px;
    background: var(--accent);
  }
  .brand-name {
    color: var(--ink);
    font-weight: 500;
    font-size: 22px;
    line-height: 1.15;
    letter-spacing: 0.5px;
  }
</style>
</head>
<body>
  <section class="card card--contact" aria-label="Business card, contact side">
    <svg class="contact-panel" viewBox="0 0 443 264" preserveAspectRatio="none" aria-hidden="true">
      <polygon points="116,0 443,0 443,264 145,264" fill="var(--card-black)"/>
    </svg>
    <div class="contact-details">
      <p class="contact-name">DORAN KELBRATH</p>
      <p class="contact-role">Partner</p>
      <p class="contact-line">0461 738 524
        <svg viewBox="0 0 10 10" aria-hidden="true"><path d="M2 1h2l1 2-1.2 1a5 5 0 0 0 2.2 2.2L7 5l2 1v2c0 .6-.4 1-1 1A8 8 0 0 1 1 2c0-.6.4-1 1-1z"/></svg>
      </p>
      <p class="contact-line">doran@kbtlaw.co
        <svg viewBox="0 0 10 10" aria-hidden="true"><path d="M0 2h10v6H0z M0 2l5 3.5L10 2" stroke="var(--card-black)" stroke-width="0.8"/></svg>
      </p>
      <p class="contact-line">www.kbtlaw.co
        <svg viewBox="0 0 10 10" aria-hidden="true"><circle cx="5" cy="5" r="4.5"/></svg>
      </p>
      <p class="contact-address">Level 3, 118 Wendmore<br>Street, Sydney NSW 2000</p>
    </div>
  </section>

  <section class="card card--brand" aria-label="Business card, brand side">
    <div class="brand-lockup">
      <span class="brand-square" aria-hidden="true"></span>
      <p class="brand-name">KELBRATH<br>BRANDT TOLLEY<br>LEGAL</p>
    </div>
  </section>
</body>
</html>
```